we can communicate on this, but i want to follow the approach we took on Pellew|Marsh & Quinlan but i feel the card front needs the black background and the platinum and gold logo. The back? I am open. we can use the same info from PM&Q. Velmont Arc is an enhanced equity investment fund - basically a very exclusive boutique hedge fund that uses only stock options. very advanced things. hope you are interested

Contact Information for Business Card

Dr. Lewis T. Brennick, CFA
Scientifique de fusée financière
701.555.0143
LTBquant47@mailvantor.com

4718 Willow Creek Bend W.
West Fargo, ND 58078

No web site

Colors

Designer to choose colors to be used in the design.

Requirements
Nice to have
• I tend to prefer the most visible applications of the logo to include logo and name, the logo version with a black background and the gold and platinum components separated by the black. I see this working well for a single side (logo and name - this is card front to me).
• I am fairly open to other treatments on the reverse side with the data. To me, it makes sense to have a different color rendition of the logo on the reverse and it may be a muted black tone on tone or an oversized portion that would have spot UV. Or, the reverse may play with colors and layout
Should not have
• Other colors = no no
• Decorative font

```html
<!DOCTYPE html>
<html lang="en">
<head>
<meta charset="utf-8">
<title>Velmont Arc — Business Card</title>
<link href="https://fonts.googleapis.com/css2?family=Roboto:wght@400;500;700&display=swap" rel="stylesheet">
<style>
  :root {
    --backdrop: #2b2b2c;
    --card: #151515;
    --platinum: #b9b9bb;
    --gold: #d4ae3a;
    --white: #f2f2f2;
    --rule: #8a8a8a;
  }
  * { margin: 0; padding: 0; box-sizing: border-box; }
  html, body {
    width: 1200px; height: 960px; overflow: hidden;
    background: var(--backdrop);
    font-family: "Roboto", sans-serif;
  }
  .canvas { position: relative; width: 1200px; height: 960px; }
  .card {
    position: absolute;
    width: 630px; height: 360px;
    background: var(--card);
    border-radius: 4px;
    box-shadow: 0 18px 40px rgba(0,0,0,.45);
  }
  .card--front { left: 110px; top: 100px; }
  .card--back { left: 460px; top: 500px; }

  .brand { display: flex; flex-direction: column; align-items: center; gap: 18px; }
  .brand__dot { border-radius: 50%; }
  .brand__name { font-weight: 500; letter-spacing: 3px; text-transform: uppercase; white-space: nowrap; }

  .card--front .brand { position: absolute; left: 0; right: 0; top: 96px; }
  .card--front .brand__dot { background: var(--platinum); width: 110px; height: 110px; }
  .card--front .brand__name { color: var(--platinum); font-size: 40px; }

  .card--back .brand { position: absolute; left: 30px; width: 250px; top: 112px; }
  .card--back .brand__dot { background: var(--gold); width: 78px; height: 78px; }
  .card--back .brand__name { color: var(--white); font-size: 26px; }

  .divider {
    position: absolute; left: 300px; top: 70px;
    width: 1px; height: 220px; background: var(--rule);
  }
  .details { position: absolute; left: 328px; top: 76px; color: var(--white); }
  .details__name { color: var(--gold); font-weight: 700; font-size: 20px; white-space: nowrap; }
  .details__name .prefix, .details__name .suffix { font-size: 13px; font-weight: 500; }
  .details__title { font-size: 14px; margin-top: 4px; }
  .details__address { font-size: 14px; line-height: 1.4; margin-top: 18px; }
  .details__contact { list-style: none; margin-top: 18px; font-size: 14px; line-height: 1.6; }
  .details__contact li { display: flex; align-items: center; gap: 9px; }
  .details__contact svg { width: 12px; height: 12px; flex: none; }
</style>
</head>
<body>
<main class="canvas">
  <section class="card card--front" aria-label="Card front">
    <div class="brand">
      <span class="brand__dot"></span>
      <span class="brand__name">Velmont Arc</span>
    </div>
  </section>

  <section class="card card--back" aria-label="Card back">
    <div class="brand">
      <span class="brand__dot"></span>
      <span class="brand__name">Velmont Arc</span>
    </div>
    <div class="divider"></div>
    <div class="details">
      <p class="details__name"><span class="prefix">Dr.</span> Lewis T. Brennick, <span class="suffix">CFA</span></p>
      <p class="details__title">Scientifique des Fusées Financières</p>
      <p class="details__address">4718 Willow Creek Bend W.<br>West Fargo, ND 58078</p>
      <ul class="details__contact">
        <li>
          <svg viewBox="0 0 12 12" fill="none" stroke="#d4ae3a" stroke-width="1.4"><rect x="3" y="0.8" width="6" height="10.4" rx="1"/><line x1="5" y1="9.3" x2="7" y2="9.3"/></svg>
          701.555.0143
        </li>
        <li>
          <svg viewBox="0 0 12 12" fill="#d4ae3a"><path d="M0 2.5h12v7H0z"/><path d="M0 2.5l6 4 6-4" stroke="#151515" stroke-width="1" fill="none"/></svg>
          LTBquant47@mailvantor.com
        </li>
      </ul>
    </div>
  </section>
</main>
</body>
</html>
```